Fresh, modern, fun business card for pediatric dental practice

Need a business card for fresh, modern, fun pediatric dental practice

Clean look that matches our website's font and colors

We prefer the look of curved corners on business cards

Target Market(s)

parents (mothers) of young children, professionals, mid-high class

Industry/Entity Type

Dental

Contact Information for Business Card

Maplebrook Pediatric Dentistry
482 Quarry Lane
Suite 517
Lititz, PA 17543
717.555.0193
www.maplebrookkidsdental.example

Mei-Ran Tsai, DMD
Corinne Walbeck, DMD
(we are working on our email address, but we would like that on the card as well)

Font styles to use
Sans Serif

Requirements
Must have
• All info; we would also like to make cards for individual staff members
• colors from our website and color palatte, attatched
• use same font and design as website for branding
Nice to have
• clean, simple card that has a pop of color
• we would like to see a few designs with our tag line "where smiles get brighter"
• we are not sure if we want to have it on there or not
• we would like to see a few designs incorporating the ribbon graphic on our website where the word WELCOME is

```html
<!DOCTYPE html>
<html lang="en">
<head>
<meta charset="utf-8">
<title>Maplebrook Pediatric Dentistry – Business Card</title>
<link rel="stylesheet" href="https://fonts.googleapis.com/css2?family=Open+Sans:wght@400;600;700&display=swap">
<style>
  :root {
    --backdrop: #ece9e5;
    --card-white: #ffffff;
    --sun-yellow: #f7b82a;
    --brand-gold: #f3ae1a;
    --smile-magenta: #d12f94;
    --ink: #2f2f2f;
    --back-charcoal: #3a3938;
    --back-text: #ffffff;
  }
  * { box-sizing: border-box; margin: 0; padding: 0; }
  html, body {
    width: 1200px; height: 900px; overflow: hidden;
    background: var(--backdrop);
    font-family: "Open Sans", sans-serif;
  }
  .stage { position: relative; width: 1200px; height: 900px; }

  .card {
    position: absolute;
    border-radius: 14px;
    overflow: hidden;
    box-shadow: 0 6px 18px rgba(0,0,0,.18);
  }

  /* Front */
  .card--front { left: 78px; top: 35px; width: 587px; height: 362px; background: var(--card-white); }
  .card-front__bands { position: absolute; inset: 0; }
  .brand-mark {
    position: absolute; left: 0; right: 0; top: 58px;
    display: flex; flex-direction: column; align-items: center; gap: 16px;
  }
  .brand-mark__dot { width: 40px; height: 40px; border-radius: 50%; background: var(--brand-gold); }
  .brand-mark__name { color: var(--brand-gold); font-weight: 600; font-size: 31px; letter-spacing: .5px; white-space: nowrap; }

  .doctors {
    position: absolute; top: 247px; right: 300px;
    text-align: right; color: var(--ink); font-weight: 700; font-size: 17px; line-height: 23px;
    white-space: nowrap;
  }
  .emails {
    position: absolute; top: 250px; left: 297px;
    color: var(--ink); font-size: 13px; line-height: 23px; list-style: none;
    white-space: nowrap;
  }
  .emails li { display: flex; align-items: center; gap: 6px; }
  .emails svg { width: 11px; height: 8px; flex: none; }
  .contact-line {
    position: absolute; left: 0; right: 0; top: 312px;
    text-align: center; color: var(--ink); font-size: 15px; white-space: nowrap;
  }
  .contact-line b { font-weight: 700; }

  /* Back */
  .card--back { left: 389px; top: 505px; width: 566px; height: 352px; background: var(--back-charcoal); }
  .back-pattern { position: absolute; inset: 0; background: var(--back-charcoal); }
  .back-mark {
    position: absolute; left: 0; right: 0; top: 62px;
    display: flex; flex-direction: column; align-items: center; gap: 18px; color: var(--back-text);
  }
  .back-mark__dot { width: 56px; height: 56px; border-radius: 50%; background: var(--back-text); }
  .back-mark__name { font-weight: 600; font-size: 38px; }
  .back-address {
    position: absolute; left: 0; right: 0; top: 259px;
    text-align: center; color: var(--back-text); font-size: 17px; line-height: 24px;
  }
  .back-address strong { font-weight: 700; display: block; }
</style>
</head>
<body>
<main class="stage">

  <section class="card card--front" aria-label="Business card front">
    <svg class="card-front__bands" width="587" height="362" viewBox="0 0 587 362" aria-hidden="true">
      <polygon points="0,198 400,198 380,225 0,225" fill="var(--smile-magenta)"/>
      <polygon points="0,229 384,229 412,190 587,190 587,362 0,362" fill="var(--sun-yellow)"/>
    </svg>

    <div class="brand-mark">
      <span class="brand-mark__dot"></span>
      <span class="brand-mark__name">Maplebrook Pediatric Dentistry</span>
    </div>

    <div class="doctors">
      <p>Mei-Ran Tsai, DMD</p>
      <p>Corinne Walbeck, DMD</p>
    </div>

    <ul class="emails">
      <li><svg viewBox="0 0 12 9"><rect width="12" height="9" fill="var(--ink)"/><path d="M0 0 L6 5 L12 0" stroke="var(--sun-yellow)" fill="none" stroke-width="1.2"/></svg>Mei-ran@maplebrookkidsdental.example</li>
      <li><svg viewBox="0 0 12 9"><rect width="12" height="9" fill="var(--ink)"/><path d="M0 0 L6 5 L12 0" stroke="var(--sun-yellow)" fill="none" stroke-width="1.2"/></svg>Corinne@maplebrookkidsdental.example</li>
    </ul>

    <p class="contact-line"><b>P:</b> 717.555.0193 | <b>W:</b> www.maplebrookkidsdental.example</p>
  </section>

  <section class="card card--back" aria-label="Business card back">
    <div class="back-pattern" role="img" aria-label="Repeating faint gold brand pattern on charcoal"></div>
    <div class="back-mark">
      <span class="back-mark__dot"></span>
      <span class="back-mark__name">Maplebrook</span>
    </div>
    <p class="back-address">
      <strong>Maplebrook Pediatric Dentistry</strong>
      482 Quarry Lane Suite 517 Lititz, PA 17543
    </p>
  </section>

</main>
</body>
</html>
```